Dorvik Electric Ltd

Looking for a single page website and Facebook page design. I am an electrical contractor based on Vancouver Island. I do service, custom homes, residential and commercial installations. My company just started out, so I don't have any pictures of installs yet. I have 25 years experience. I would like the colors to be my logo colors black and I have a black Brandt Halvard that will be my vehicle which I will have a wrap for.
Updates

I just posted the contest today, not sure why the deadline is the same day.

Industry/Entity Type

Electrician

Requirements
Must have
• Services provided, About me section, quote section,
Nice to have
• I am not quite sure yet, I need to see some designs first .

```html
<!DOCTYPE html>
<html lang="en">
<head>
<meta charset="utf-8">
<title>Dorvik Electric Ltd</title>
<link href="https://fonts.googleapis.com/css2?family=Montserrat:wght@600;700;800&family=Roboto:ital,wght@0,400;0,500;0,700;1,400&display=swap" rel="stylesheet">
<style>
:root{
  --yellow:#eeaa14;
  --black:#0d0d0d;
  --ink:#1a1a1a;
  --text:#555;
  --white:#fff;
  --footer:#161616;
}
*{margin:0;padding:0;box-sizing:border-box}
html,body{width:1200px;height:4380px;overflow:hidden}
body{position:relative;background:var(--white);font-family:'Roboto',Arial,sans-serif;color:var(--text)}
.abs{position:absolute}
.heading{font-family:'Montserrat',Arial,sans-serif;font-weight:700;color:var(--ink);text-transform:uppercase}
.section-title{position:absolute;left:0;width:1200px;text-align:center;font-size:38px}
.section-title::after{content:"";display:block;width:66px;height:3px;background:var(--yellow);margin:18px auto 0}
.btn{position:absolute;display:flex;align-items:center;justify-content:center;gap:6px;background:var(--yellow);color:var(--white);border-radius:26px;font-family:'Montserrat',Arial,sans-serif;font-weight:700;font-size:13px;text-transform:uppercase}
.btn svg{width:12px;height:12px}

/* header */
.site-header{left:0;top:0;width:1200px;height:85px;background:var(--black)}
.brand{left:110px;top:14px;display:flex;flex-direction:column;align-items:center;gap:4px}
.brand-mark{width:40px;height:40px;border-radius:50%;border:3px solid var(--yellow)}
.brand-name{font-family:'Montserrat',Arial,sans-serif;font-weight:700;font-size:10px;color:var(--white);text-transform:uppercase}
.nav{left:362px;top:33px;display:flex;gap:22px;font-family:'Roboto',Arial,sans-serif;font-weight:500;font-size:14px;color:var(--white)}
.nav .active{color:var(--yellow);border-bottom:2px solid var(--yellow);padding-bottom:5px}
.call-box{left:867px;top:0;width:221px;height:85px;background:var(--yellow);padding:22px 0 0 36px;color:var(--white)}
.call-box small{display:block;font-size:13px;font-weight:500}
.call-box strong{display:block;font-size:21px;font-weight:500;margin-top:3px}
.call-icon{left:841px;top:19px;width:48px;height:48px;border-radius:50%;background:var(--white);border:3px solid var(--yellow);display:flex;align-items:center;justify-content:center}

/* hero */
.hero{left:0;top:85px;width:1200px;height:643px;background:linear-gradient(180deg,#8fb3d8 0%,#c7d8e6 32%,#8b8a80 48%,#6c6e68 70%,#4f514f 100%)}
.hero-title{left:0;top:160px;width:1200px;text-align:center;font-size:68px;line-height:70px;font-weight:800;color:var(--black)}
.hero-arrow{width:52px;height:52px;border-radius:50%;background:rgba(40,40,40,.7);display:flex;align-items:center;justify-content:center}
.scroll-down{left:576px;top:704px;width:48px;height:48px;border-radius:50%;background:var(--white);border:2px dashed var(--yellow);display:flex;align-items:center;justify-content:center}

/* about */
.about-photo-main{left:235px;top:830px;width:528px;height:377px;background:linear-gradient(160deg,#4a5568 0%,#b78a5c 55%,#8d8c88 100%)}
.about-photo-small{left:110px;top:1018px;width:333px;height:269px;border:5px solid var(--white);background:linear-gradient(180deg,#9aa7b4 0%,#3a3a3a 50%,#5e7a3e 100%)}
.badge{left:171px;top:866px;width:124px;height:124px;border-radius:50%;background:var(--yellow);border:5px solid var(--white);box-shadow:0 0 0 2px var(--yellow);display:flex;flex-direction:column;align-items:center;justify-content:center;color:var(--ink);font-size:14px;line-height:16px}
.badge b{font-size:28px;line-height:30px;font-family:'Montserrat',Arial,sans-serif}
.about-panel{left:620px;top:913px;width:468px;height:390px;background:var(--white);padding:22px 0 0 28px}
.about-panel h2{font-size:38px}
.about-panel h2::after{content:"";display:block;width:64px;height:3px;background:var(--yellow);margin-top:16px}
.about-panel p{font-size:14px;line-height:25.5px;text-align:justify;margin-top:18px;color:#555}

/* services */
.service{width:434px;height:434px;border-radius:50%;border:17px solid var(--yellow);background:var(--white);text-align:center}
.service.featured{background:radial-gradient(circle,#f3f1ec 0%,#dcdad3 100%)}
.service-icon{position:absolute;left:174px;top:52px;width:86px;height:86px;border-radius:50%;background:var(--yellow);display:flex;align-items:center;justify-content:center}
.service h3{position:absolute;left:0;width:400px;top:165px;font-family:'Roboto',Arial,sans-serif;font-weight:500;font-size:20px;color:var(--ink);text-transform:uppercase}
.service p{position:absolute;left:40px;width:320px;top:200px;font-size:13.5px;line-height:26px;color:#555}
.service .btn{left:118px;top:294px;width:164px;height:48px}

/* projects */
.project{background:linear-gradient(150deg,#6f6f6f,#c8c8c8)}
.eye{left:574px;top:2206px;width:52px;height:52px;border-radius:50%;background:var(--yellow);display:flex;align-items:center;justify-content:center}

/* testimonials */
.band{left:0;top:2813px;width:1200px;height:318px;background:var(--yellow)}
.testimonial-photo{left:518px;top:2759px;width:570px;height:415px;background:linear-gradient(200deg,#f3c466 0%,#d77b2a 40%,#5b5f66 100%)}
.testimonial-card{left:112px;top:2910px;width:487px;height:286px;background:var(--white);padding:34px 30px 0}
.testimonial-card h2{font-size:32px}
.testimonial-card h2::after{content:"";display:block;width:64px;height:3px;background:var(--yellow);margin-top:12px}
.testimonial-card blockquote{font-style:italic;font-size:14px;line-height:25.5px;color:#555;margin-top:16px;text-align:justify;padding-left:6px}
.client{left:36px;top:220px}
.client b{display:block;font-size:19px;font-weight:500;color:var(--ink)}
.client span{font-size:13px;color:#555}

/* news */
.news{width:310px}
.news-photo{width:310px;height:233px}
.news-date{margin-top:20px;font-size:13px;color:var(--ink);padding-left:16px;display:flex;align-items:center;gap:5px}
.news h3{margin:12px 0 0 16px;padding-left:16px;border-left:3px solid var(--yellow);font-family:'Roboto',Arial,sans-serif;font-weight:500;font-size:20px;line-height:30px;color:var(--ink)}
.news p{margin:14px 0 0 16px;font-size:13px;line-height:25.5px;color:#555}
.news a{display:flex;align-items:center;gap:4px;margin:6px 0 0 16px;color:var(--yellow);font-size:13px;font-weight:500;text-decoration:underline}

/* footer */
.site-footer{left:0;top:3958px;width:1200px;height:422px;background:radial-gradient(circle at 45% 30%,#2a2a2a 0%,var(--footer) 70%)}
.footer-brand{left:140px;top:4050px;width:220px;display:flex;flex-direction:column;align-items:center}
.footer-brand .brand-mark{width:110px;height:110px;border-width:5px}
.footer-brand .brand-name{font-size:18px;margin-top:12px;font-weight:600}
.social{display:flex;gap:10px;margin-top:18px}
.social span{width:32px;height:32px;border-radius:50%;border:1.5px solid var(--white)}
.footer-col{top:4052px;color:var(--white)}
.footer-col h4{font-family:'Montserrat',Arial,sans-serif;font-weight:700;font-size:16px;text-transform:uppercase;margin-bottom:22px}
.footer-col li{list-style:none;font-size:13px;line-height:27.5px}
.contact-item{display:flex;gap:10px;margin-bottom:10px;font-size:13px;line-height:19px}
.contact-item b{display:block;font-weight:700}
.copyright{left:0;top:4320px;width:1200px;text-align:center;color:var(--white);font-size:14px}
.to-top{left:1109px;top:4268px;width:36px;height:36px;border-radius:50%;background:var(--yellow);display:flex;align-items:center;justify-content:center}
</style>
</head>
<body>

<header class="site-header abs">
  <div class="brand abs"><span class="brand-mark"></span><span class="brand-name">Dorvik Electric Ltd</span></div>
  <nav class="nav abs">
    <span class="active">Home</span><span>About us</span><span>Services</span><span>Testimonials</span><span>Blog</span><span>Contact us</span>
  </nav>
  <div class="call-box abs"><small>Call us Today :</small><strong>+1 888 888 8888</strong></div>
  <div class="call-icon abs"><svg width="18" height="18" viewBox="0 0 24 24"><path fill="#eeaa14" d="M6.6 10.8a15 15 0 006.6 6.6l2.2-2.2c.3-.3.7-.4 1-.2 1.1.4 2.3.6 3.6.6.6 0 1 .4 1 1V20c0 .6-.4 1-1 1C10.6 21 3 13.4 3 4c0-.6.4-1 1-1h3.5c.6 0 1 .4 1 1 0 1.3.2 2.5.6 3.6.1.3 0 .7-.2 1z"/></svg></div>
</header>

<section class="hero abs" role="img" aria-label="Residential neighbourhood seen from a shingled rooftop">
</section>
<h1 class="hero-title heading abs">Dorvik<br>Electric Ltd</h1>
<div class="btn" style="left:518px;top:316px;width:164px;height:48px">Get Started <svg viewBox="0 0 12 12"><circle cx="6" cy="6" r="6" fill="#fff"/><path d="M5 3.5 7.5 6 5 8.5" stroke="#eeaa14" stroke-width="1.6" fill="none"/></svg></div>
<div class="hero-arrow abs" style="left:30px;top:362px"><svg width="14" height="14" viewBox="0 0 14 14"><path d="M9 2 4 7l5 5" stroke="#fff" stroke-width="2" fill="none"/></svg></div>
<div class="hero-arrow abs" style="left:1118px;top:362px"><svg width="14" height="14" viewBox="0 0 14 14"><path d="M5 2l5 5-5 5" stroke="#fff" stroke-width="2" fill="none"/></svg></div>
<div class="scroll-down abs"><svg width="14" height="14" viewBox="0 0 14 14"><path d="M7 1v10M3 7l4 4 4-4" stroke="#111" stroke-width="2.2" fill="none"/></svg></div>

<section class="about">
  <div class="about-photo-main abs" role="img" aria-label="Two electricians working on a roof at sunset"></div>
  <div class="about-photo-small abs" role="img" aria-label="Modern dark house with solar panels and a pool"></div>
  <div class="badge abs"><b>25</b>Years<br>Experience</div>
  <div class="about-panel abs">
    <h2 class="heading">About Us</h2>
    <p>Lorem ipsum dolor sit amet, consectetur adipiscing elit, sed do eiusmod tempor incididunt ut labore et dolore magna aliqua. Ut enim ad minim veniam, quis nostrud exercitation ullamco laboris nisi ut aliquip ex ea commodo consequat.</p>
    <p>Duis aute irure dolor in reprehenderit in voluptate velit esse cillum dolore eu fugiat nulla pariatur.Lorem ipsum dolor sit amet, consec tetur adipiscing elit, sed do eiusmod tempor incididunt</p>
  </div>
  <div class="btn" style="left:648px;top:1238px;width:163px;height:48px">Learn More <svg viewBox="0 0 12 12"><circle cx="6" cy="6" r="6" fill="#fff"/><path d="M5 3.5 7.5 6 5 8.5" stroke="#eeaa14" stroke-width="1.6" fill="none"/></svg></div>
</section>

<h2 class="section-title heading" style="top:1380px">Our Services</h2>

<div class="service abs" style="left:-18px;top:1471px">
  <div class="service-icon"><svg width="44" height="44" viewBox="0 0 44 44" fill="none" stroke="#111" stroke-width="2"><rect x="8" y="10" width="26" height="26"/><path d="M12 32l18-18 4 4-18 18H12z"/><path d="M8 16h6M8 22h4M8 28h6"/></svg></div>
  <h3>Custom Homes</h3>
  <p>Lorem ipsum dolor sit amet, consectetur adipi scing elit, sed do eiusmod tempor incididunt ut labore et dolore magna aliqua.</p>
  <div class="btn">Learn More <svg viewBox="0 0 12 12"><circle cx="6" cy="6" r="6" fill="#fff"/><path d="M5 3.5 7.5 6 5 8.5" stroke="#eeaa14" stroke-width="1.6" fill="none"/></svg></div>
</div>
<div class="service featured abs" style="left:383px;top:1471px" role="img" aria-label="Electrician installing ceiling wiring">
  <div class="service-icon"><svg width="44" height="44" viewBox="0 0 44 44" fill="none" stroke="#111" stroke-width="2"><path d="M6 22 22 8l16 14"/><rect x="11" y="20" width="22" height="16"/><rect x="18" y="26" width="8" height="10"/><path d="M6 38h32"/></svg></div>
  <h3>Residential Installations</h3>
  <p>Lorem ipsum dolor sit amet, consectetur adipi scing elit, sed do eiusmod tempor incididunt ut labore et dolore magna aliqua.</p>
  <div class="btn">Learn More <svg viewBox="0 0 12 12"><circle cx="6" cy="6" r="6" fill="#fff"/><path d="M5 3.5 7.5 6 5 8.5" stroke="#eeaa14" stroke-width="1.6" fill="none"/></svg></div>
</div>
<div class="service abs" style="left:784px;top:1471px">
  <div class="service-icon"><svg width="44" height="44" viewBox="0 0 44 44" fill="none" stroke="#111" stroke-width="2"><path d="M8 16h28l-3-8H11z"/><rect x="9" y="16" width="26" height="20"/><rect x="13" y="22" width="8" height="14"/><rect x="24" y="22" width="8" height="7"/></svg></div>
  <h3>Commercial Installations</h3>
  <p>Lorem ipsum dolor sit amet, consectetur adipi scing elit, sed do eiusmod tempor incididunt ut labore et dolore magna aliqua.</p>
  <div class="btn">Learn More <svg viewBox="0 0 12 12"><circle cx="6" cy="6" r="6" fill="#fff"/><path d="M5 3.5 7.5 6 5 8.5" stroke="#eeaa14" stroke-width="1.6" fill="none"/></svg></div>
</div>

<h2 class="section-title heading" style="top:2000px">Our Projects</h2>
<div class="project abs" style="left:110px;top:2094px;width:318px;height:274px" role="img" aria-label="Electrician working on a wall electrical panel"></div>
<div class="project abs" style="left:441px;top:2094px;width:317px;height:274px" role="img" aria-label="Electrician installing a pendant light"></div>
<div class="project abs" style="left:772px;top:2094px;width:316px;height:274px;background:linear-gradient(150deg,#1e1e22,#8a8f99)" role="img" aria-label="Electrician fitting ceiling lights"></div>
<div class="eye abs"><svg width="20" height="14" viewBox="0 0 20 14"><path d="M1 7s3.5-6 9-6 9 6 9 6-3.5 6-9 6-9-6-9-6z" fill="#111"/><circle cx="10" cy="7" r="3" fill="#eeaa14"/></svg></div>
<div class="project abs" style="left:110px;top:2382px;width:484px;height:273px" role="img" aria-label="Electrician wiring a ceiling frame"></div>
<div class="project abs" style="left:606px;top:2382px;width:482px;height:273px;background:linear-gradient(150deg,#d9d9d9,#8a8a8a)" role="img" aria-label="Electrician on a ladder with cable"></div>

<div class="band abs"></div>
<div class="testimonial-photo abs" role="img" aria-label="Worker installing roof panels at sunset"></div>
<div class="testimonial-card abs">
  <h2 class="heading">What Our Clients Say</h2>
  <blockquote>"Lorem ipsum dolor sit amet, consectetur adipiscing elit, sed do eiusmod tempor incididunt ut labore et dolore magna aliqua. Ut enim ad minim veniam, quis nostrud exercitation ullamco laboris nisi ut aliquip ex ea commodo consequat. "</blockquote>
  <div class="client abs"><b>John Doe</b><span>Company name</span></div>
  <svg class="abs" style="left:362px;top:238px" width="80" height="24" viewBox="0 0 80 24" fill="none" stroke-width="2.5"><path d="M30 12H4m8-8-8 8 8 8" stroke="#aaa"/><path d="M46 12h28m-8-8 8 8-8 8" stroke="#eeaa14"/></svg>
</div>

<h2 class="section-title heading" style="top:3310px">News &amp; Update</h2>
<article class="news abs" style="left:110px;top:3407px">
  <div class="news-photo" role="img" aria-label="Electrician working on overhead cable trays" style="background:linear-gradient(150deg,#3d4a5c,#a7b0bb)"></div>
  <div class="news-date"><svg width="11" height="11" viewBox="0 0 11 11"><rect x="0.5" y="1.5" width="10" height="9" fill="#111"/></svg>Jan 20, 2022</div>
  <h3>Lorem ipsum dolor sit am et, consectetur</h3>
  <p>Lorem ipsum dolor sit amet, consect etur adipiscing elit, sed do eiusmod tempor incididunt ut</p>
  <a>LEARN MORE <svg width="12" height="12" viewBox="0 0 12 12"><circle cx="6" cy="6" r="6" fill="#eeaa14"/><path d="M5 3.5 7.5 6 5 8.5" stroke="#fff" stroke-width="1.6" fill="none"/></svg></a>
</article>
<article class="news abs" style="left:445px;top:3407px">
  <div class="news-photo" role="img" aria-label="Electrician sorting coloured wires" style="background:linear-gradient(150deg,#4a7fb0,#e2a248)"></div>
  <div class="news-date"><svg width="11" height="11" viewBox="0 0 11 11"><rect x="0.5" y="1.5" width="10" height="9" fill="#111"/></svg>Jan 20, 2022</div>
  <h3>Lorem ipsum dolor sit am et, consectetur</h3>
  <p>Lorem ipsum dolor sit amet, consect etur adipiscing elit, sed do eiusmod tempor incididunt ut</p>
  <a>LEARN MORE <svg width="12" height="12" viewBox="0 0 12 12"><circle cx="6" cy="6" r="6" fill="#eeaa14"/><path d="M5 3.5 7.5 6 5 8.5" stroke="#fff" stroke-width="1.6" fill="none"/></svg></a>
</article>
<article class="news abs" style="left:780px;top:3407px">
  <div class="news-photo" role="img" aria-label="Technician checking outdoor air units" style="background:linear-gradient(150deg,#d8d8d8,#e38a2e 60%,#5a5a5a)"></div>
  <div class="news-date"><svg width="11" height="11" viewBox="0 0 11 11"><rect x="0.5" y="1.5" width="10" height="9" fill="#111"/></svg>Jan 20, 2022</div>
  <h3>Lorem ipsum dolor sit am et, consectetur</h3>
  <p>Lorem ipsum dolor sit amet, consect etur adipiscing elit, sed do eiusmod tempor incididunt ut</p>
  <a>LEARN MORE <svg width="12" height="12" viewBox="0 0 12 12"><circle cx="6" cy="6" r="6" fill="#eeaa14"/><path d="M5 3.5 7.5 6 5 8.5" stroke="#fff" stroke-width="1.6" fill="none"/></svg></a>
</article>

<footer class="site-footer abs">
</footer>
<div class="footer-brand abs">
  <span class="brand-mark"></span>
  <span class="brand-name">Dorvik Electric Ltd</span>
  <div class="social"><span></span><span></span><span></span><span></span></div>
</div>
<div class="footer-col abs" style="left:432px">
  <h4>Quick Links</h4>
  <ul><li>Home</li><li>About us</li><li>Our Services</li><li>News</li><li>Contact Us</li></ul>
</div>
<div class="footer-col abs" style="left:613px">
  <h4>About Company</h4>
  <ul><li>Legal Information</li><li>Terms &amp; Condition</li><li>Privacy Policy</li><li>Support</li><li>Site Map</li></ul>
</div>
<div class="footer-col abs" style="left:843px">
  <h4>Contact Us</h4>
  <div class="contact-item"><svg width="14" height="14" viewBox="0 0 24 24"><path fill="#eeaa14" d="M6.6 10.8a15 15 0 006.6 6.6l2.2-2.2c.3-.3.7-.4 1-.2 1.1.4 2.3.6 3.6.6.6 0 1 .4 1 1V20c0 .6-.4 1-1 1C10.6 21 3 13.4 3 4c0-.6.4-1 1-1h3.5c.6 0 1 .4 1 1 0 1.3.2 2.5.6 3.6.1.3 0 .7-.2 1z"/></svg><div><b>Phone</b>+1 (888) 888-8888</div></div>
  <div class="contact-item"><svg width="14" height="14" viewBox="0 0 14 14"><rect x="1" y="3" width="12" height="9" fill="#eeaa14"/><path d="M1 3l6 5 6-5" stroke="#161616" fill="none"/></svg><div><b>Email</b>info@companyname.com</div></div>
  <div class="contact-item"><svg width="14" height="14" viewBox="0 0 14 14"><path d="M7 1a4 4 0 014 4c0 3-4 8-4 8S3 8 3 5a4 4 0 014-4z" fill="#eeaa14"/><circle cx="7" cy="5" r="1.5" fill="#161616"/></svg><div><b>Location</b>311 S Lorem ipsum dolor sit amet,<br>consectetur adipiscing elit,</div></div>
</div>
<div class="to-top abs"><svg width="14" height="14" viewBox="0 0 14 14"><path d="M3 9l4-4 4 4" stroke="#fff" stroke-width="2" fill="none"/></svg></div>
<p class="copyright abs">2022 Copyright Dorvik Electric Ltd &nbsp;| All Rights Reserved</p>

</body>
</html>
```